Maple Lantern Productions web site

I need to build a website for a new company I am launching next month. Maple Lantern Productions is a company based in New England that provides sound, lighting, and audio visual services to weddings, corporate, and any other cusomer base looking for quality service for a fair price. Looking for somebody to do a full site not just the image files. I am looking to keep the colors of my logo (orange and black) and possibly grey and white. I am looking to build my site very similar to brightvaleevents.example, which is owned by a friend of mine. I like how he has the big pictures that load in to the site and the basic menu items. I'll need a gallery of photos. The designs should communicate quality, value and trust.
My website address is maplelanternco.example.
Updates

Hi and thanks to everyone for posting such great ideas for our new design.I have some items that I'd like to ask you all to focus on in your revisions.I like how http://www.brightvaleevents.example/ website has five or six high res pictures that change in a slideshow format with a caption that loads in for each one for the different types of services. Try and capture pics like these and with teh same headings as he has. The basic menu designs have been interesting.I am more fond of the menus that are more white with some orange as I dont want it to be too dark. I'm curious to see how your galleries will work and if i'll be able to edit the pages myself? I have some more info on the company for you to fill in:website address is ciderhouseco.comemail: info@ciderhouseco.comaddress: Maple Lantern Productions57 Littlefield StreetAvon, MA 02417"New England's finest DJ's, lighting and sound, video and more. Creating memories one perfect event at a time."Put this under the loading pictures as a tagline.About Cider HouseCider House Productions is a collection of New England's finest talent, ready to make your next event the one you've dreamed of. We have the skills and expertise to deliver your vision of your perfect event. From elegant weddings to themed mitzvah's, corporate av, videography and detail lighting, we offer all of the elements to make your event a success. Added Wednesday, March 1, 2017

Designer's Please also make sure that your design flows well on any device it is being viewed on as well. Thanks. Added Wednesday, March 1, 2017

Project Deadline Extended Reason: Hello designerThank you all very much for your hard work on our project. Im sorry but i need to extend the date of my project. Our parent conpany Rook Nine Prodactions sponsors Bay Youth Assemblies and we are currently at their leadership conference on the Cape. I will be back in on Monday and with your help will get this finished by Thursday the 16th. Thanks Added Thursday, March 9, 2017

Project Deadline Extended Reason: One of the designers is not responding so I now have to make revisions with other designers. I hope to get this website done over the weekends so please get your revisions as soon as possible. Thank you. I am also upgrading the budget another $75 to hopefully get some more interest on my project. Added Wednesday, March 15, 2017

Target Market(s)

Wedding - Corporate -

Industry/Entity Type

It Company

Coding

Coded - Design and coding required

Number of Pages Required

5+ page

Font styles to use
Sans Serif

Requirements
Must have
• Photo Gallery - I want to be able to edit it myself
Nice to have
• I like the look of my friends website brightvaleevents.example

```html
<!DOCTYPE html>
<html lang="en">
<head>
<meta charset="utf-8">
<title>Maple Lantern Productions</title>
<link href="https://fonts.googleapis.com/css2?family=Open+Sans:wght@400;600;700&family=Roboto:wght@400;500;700&display=swap" rel="stylesheet">
<style>
:root{
  --orange:#ef7536;
  --orange-dark:#e0632a;
  --ink:#222222;
  --text:#3c3c3c;
  --muted:#666666;
  --blush:#fdf4f0;
  --footer:#262626;
  --footer-line:#4a4a4a;
  --white:#ffffff;
}
*{margin:0;padding:0;box-sizing:border-box}
html,body{width:1200px;height:3727px;overflow:hidden;background:var(--white)}
body{font-family:"Open Sans",Arial,sans-serif;color:var(--text);position:relative}
h1,h2,h3,h4,.nav a,.btn{font-family:"Roboto",Arial,sans-serif}

/* header */
.site-header{position:absolute;top:0;left:0;width:1200px;height:130px;background:var(--white);z-index:3}
.header-band{position:absolute;top:0;right:0;width:800px;height:130px}
.brand{position:absolute;left:100px;top:25px;display:flex;align-items:center;gap:14px}
.brand-dot{width:72px;height:72px;border-radius:50%;background:var(--orange);flex:none}
.brand-name{font-family:"Roboto",sans-serif;font-weight:700;font-size:24px;line-height:28px;color:var(--ink);width:220px;text-transform:uppercase}
.contact-strip{position:absolute;right:100px;top:26px;display:flex;gap:32px;color:var(--white);font-size:17px;font-weight:600;white-space:nowrap}
.contact-strip span{display:flex;align-items:center;gap:10px}
.nav{position:absolute;right:100px;top:86px;display:flex;gap:40px;white-space:nowrap}
.nav a{color:var(--white);text-decoration:none;font-size:14px;font-weight:500;text-transform:uppercase}

/* hero */
.hero{position:absolute;top:130px;left:0;width:1200px;height:555px;background:linear-gradient(135deg,#2b1a3d 0%,#5a3a8a 35%,#3a2440 60%,#1e1418 100%)}
.hero-cut{position:absolute;left:0;bottom:0;width:1200px;height:60px}
.hero-title{position:absolute;left:50%;transform:translateX(-50%);top:193px;min-width:688px;height:79px;padding:0 30px;background:rgba(239,117,54,.92);color:var(--white);font-size:38px;font-weight:700;text-align:center;line-height:79px;text-transform:uppercase;white-space:nowrap}
.hero-sub{position:absolute;left:0;width:1200px;top:303px;text-align:center;color:var(--white);font-size:19px;font-weight:600;white-space:nowrap}
.dots{position:absolute;left:542px;top:450px;display:flex;gap:10px}
.dots i{width:15px;height:15px;border-radius:50%;border:2px solid var(--white);display:block}
.dots i.on{background:var(--orange);border-color:var(--orange)}

/* welcome */
.mark{position:absolute;left:578px;top:662px;width:44px;height:44px;border-radius:50%;background:var(--orange);z-index:2}
.section-title{color:var(--orange);font-weight:700;font-size:26px;text-transform:uppercase}
.welcome-title{position:absolute;top:738px;left:0;width:1200px;text-align:center}
.rule{display:block;width:80px;height:2px;background:var(--orange);opacity:.6}
.welcome-text{position:absolute;top:790px;left:130px;width:940px;text-align:center;font-size:13.5px;line-height:27px}
.services{position:absolute;top:890px;left:84px;width:1030px;display:flex;justify-content:space-between}
.service{width:200px;text-align:center}
.service svg{display:block;margin:0 auto}
.service h3{font-size:17px;font-weight:500;color:var(--ink);margin-top:12px}
.service.active h3{color:var(--orange)}
.service p{font-size:13px;line-height:19px;margin-top:12px;color:var(--text)}

/* feature rows */
.feature{position:absolute;left:0;width:1200px}
.feature.tint{background:var(--blush)}
.feature-copy{position:absolute;width:550px}
.feature-copy h2{font-size:25px;font-weight:700;color:var(--orange);text-transform:uppercase}
.feature-copy .rule{margin:14px 0 20px}
.feature-copy p{font-size:13.5px;line-height:24px;margin-bottom:10px}
.meta{font-size:12.5px;color:var(--orange);margin-bottom:12px}
.btn{display:inline-block;margin-top:16px;width:130px;height:50px;border:2px solid var(--ink);background:var(--white);font-size:14px;font-weight:700;color:var(--ink);text-align:center;line-height:46px}
.photo{position:absolute;border:6px solid #e7e2df}

/* gallery */
.gallery-title{position:absolute;top:2588px;left:0;width:1200px;text-align:center}
.gallery{position:absolute;top:2688px;left:99px;width:1000px;height:521px}
.tile{position:absolute}
.tile-brand{background:var(--orange);display:flex;align-items:center;justify-content:center;color:var(--white);font-family:"Roboto",sans-serif;font-weight:700;font-size:28px;text-transform:uppercase;text-align:center;line-height:34px}

/* footer */
.site-footer{position:absolute;top:3274px;left:0;width:1200px;height:453px;background:var(--footer);color:#dcdcdc}
.foot-brand{position:absolute;left:99px;top:75px;width:210px;text-align:center}
.foot-brand .dot{width:90px;height:90px;border-radius:50%;background:var(--white);margin:0 auto 14px}
.foot-brand .name{font-family:"Roboto",sans-serif;font-weight:700;font-size:24px;line-height:28px;color:var(--white);text-transform:uppercase}
.foot-col{position:absolute;top:98px}
.foot-col h4{font-size:16px;font-weight:500;color:var(--white);text-transform:uppercase}
.foot-col .rule{width:80px;height:2px;background:var(--white);margin:10px 0 20px;opacity:.8}
.links li{list-style:none;font-size:15px;line-height:30px;color:var(--white)}
.links li::before{content:"> ";}
.info{display:flex;gap:14px;margin-bottom:16px}
.info .ic{width:34px;height:34px;border-radius:50%;background:var(--white);flex:none;display:flex;align-items:center;justify-content:center}
.info b{display:block;font-size:15px;font-weight:600;color:var(--white);text-transform:uppercase}
.info span{font-size:13px;line-height:18px;color:#cfcfcf}
.form{display:grid;grid-template-columns:137px 137px;gap:10px}
.field{height:34px;border:1px solid #bfbfbf;font-size:12px;color:var(--white);padding:8px 8px}
.field.wide{grid-column:span 2;height:64px}
.send{width:118px;height:36px;background:var(--orange);color:var(--white);font-size:12px;line-height:36px;text-align:center;text-transform:uppercase}
.foot-rule{position:absolute;left:99px;right:99px;top:370px;height:1px;background:var(--footer-line)}
.copyright{position:absolute;top:405px;left:0;width:1200px;text-align:center;font-size:15px;font-weight:600;color:var(--white)}
</style>
</head>
<body>

<header class="site-header">
  <svg class="header-band" viewBox="0 0 800 130" preserveAspectRatio="none" aria-hidden="true"><polygon points="0,0 800,0 800,130 50,130" fill="#ef7536"/></svg>
  <div class="brand"><span class="brand-dot"></span><span class="brand-name">Maple Lantern Productions</span></div>
  <div class="contact-strip">
    <span><svg width="26" height="26" viewBox="0 0 26 26"><circle cx="13" cy="13" r="12" fill="none" stroke="#fff" stroke-width="2"/><path d="M9 7l3 3-2 2a8 8 0 004 4l2-2 3 3-2 2C11 19 7 15 7 9z" fill="#fff"/></svg>180 555 0142</span>
    <span><svg width="26" height="26" viewBox="0 0 26 26"><circle cx="13" cy="13" r="12" fill="none" stroke="#fff" stroke-width="2"/><rect x="7" y="9" width="12" height="8" fill="none" stroke="#fff" stroke-width="1.6"/><path d="M7 9l6 5 6-5" fill="none" stroke="#fff" stroke-width="1.6"/></svg>info@maplelantern.example</span>
  </div>
  <nav class="nav"><a>Home</a><a>Services</a><a>About Us</a><a>Gallery</a><a>Events</a><a>Contact Us</a></nav>
</header>

<section class="hero" role="img" aria-label="Photo of a bride and groom dancing in a softly lit venue">
  <div class="hero-title">Maple Lantern Productions</div>
  <p class="hero-sub">Maple Lantern Productions is a company based in New England</p>
  <div class="dots"><i></i><i class="on"></i><i></i><i></i><i></i></div>
  <svg class="hero-cut" viewBox="0 0 1200 60" preserveAspectRatio="none" aria-hidden="true"><path d="M0 40 Q300 0 600 30 T1200 10 L1200 60 L0 60Z" fill="#fff"/></svg>
</section>

<span class="mark"></span>
<h1 class="section-title welcome-title">Welcome to Maple Lantern Productions<span class="rule" style="margin:14px auto 0"></span></h1>
<p class="welcome-text">Maple Lantern Productions is a company based in New England that provides sound, lighting, and audio visual services to weddings, corporate, and any other cusomer base looking for quality service for a fair price.</p>

<div class="services">
  <div class="service">
    <svg width="140" height="160" viewBox="0 0 140 160"><path d="M70 4a66 66 0 0 1 20 129L70 154 50 133A66 66 0 0 1 70 4z" fill="#fff" stroke="#222" stroke-width="3"/><path d="M52 60h10l14-12v44l-14-12H52z" fill="none" stroke="#222" stroke-width="3"/><path d="M84 62l10-6M86 70h12M84 78l10 6" stroke="#222" stroke-width="3"/></svg>
    <h3>Sound</h3><p>Maple Lantern Productions is a company based in New England that provides sound.</p>
  </div>
  <div class="service active">
    <svg width="140" height="160" viewBox="0 0 140 160"><path d="M70 4a66 66 0 0 1 20 129L70 154 50 133A66 66 0 0 1 70 4z" fill="#ef7536"/><circle cx="70" cy="66" r="13" fill="none" stroke="#fff" stroke-width="3"/><path d="M70 42v-8M70 98v-8M46 66h-8M102 66h-8M53 49l-6-6M93 89l-6-6M53 83l-6 6M93 43l-6 6M62 84h16" stroke="#fff" stroke-width="3"/></svg>
    <h3>Lighting</h3><p>Maple Lantern Productions is a company based in New England that provides sound.</p>
  </div>
  <div class="service">
    <svg width="140" height="160" viewBox="0 0 140 160"><path d="M70 4a66 66 0 0 1 20 129L70 154 50 133A66 66 0 0 1 70 4z" fill="#fff" stroke="#222" stroke-width="3"/><path d="M56 42v48M70 42v48M84 42v48" stroke="#222" stroke-width="3"/><rect x="50" y="50" width="12" height="8" fill="#222"/><rect x="64" y="72" width="12" height="8" fill="#222"/><rect x="78" y="58" width="12" height="8" fill="#222"/></svg>
    <h3>Audio</h3><p>Maple Lantern Productions is a company based in New England that provides sound.</p>
  </div>
  <div class="service">
    <svg width="140" height="160" viewBox="0 0 140 160"><path d="M70 4a66 66 0 0 1 20 129L70 154 50 133A66 66 0 0 1 70 4z" fill="#fff" stroke="#222" stroke-width="3"/><circle cx="60" cy="72" r="14" fill="none" stroke="#222" stroke-width="3"/><circle cx="80" cy="72" r="14" fill="none" stroke="#222" stroke-width="3"/><path d="M54 54l6-8 6 8z" fill="#222"/><path d="M74 54l6-8 6 8z" fill="#222"/></svg>
    <h3>Wedding</h3><p>Maple Lantern Productions is a company based in New England that provides sound.</p>
  </div>
  <div class="service">
    <svg width="140" height="160" viewBox="0 0 140 160"><path d="M70 4a66 66 0 0 1 20 129L70 154 50 133A66 66 0 0 1 70 4z" fill="#fff" stroke="#222" stroke-width="3"/><path d="M52 90V48l22-8v50z" fill="#222"/><rect x="76" y="60" width="14" height="30" fill="#222"/><path d="M58 54h10M58 62h10M58 70h10" stroke="#fff" stroke-width="2"/></svg>
    <h3>Corporate</h3><p>Maple Lantern Productions is a company based in New England that provides sound.</p>
  </div>
</div>

<section class="feature tint" style="top:1225px;height:402px">
  <div class="feature-copy" style="left:99px;top:76px">
    <h2>Wedding Services</h2><span class="rule"></span>
    <p>Sed ut perspiciatis unde omnis iste natus error sit voluptatem accusantium doloremque lau dantium, totam rem aperiam, eaque ipsa quae ab illo inventore veritatis et quasi archi tecto beatae vitae dicta sunt explicabo.</p>
    <p>Nemo enim ipsam voluptatem quia voluptas sit aspernatur aut odit aut fugit, sed quia conse quuntur magni dolores eos qui ratione voluptatem sequi nesciunt. Neque porro quisquam est, qui dolorem ipsum quia dolor sit amet.</p>
    <span class="btn">Read More</span>
  </div>
  <div class="photo" role="img" aria-label="Photo of wedding guests celebrating outdoors, with a video play button" style="left:683px;top:67px;width:415px;height:298px;background:linear-gradient(135deg,#c9b28a,#6f6a4e 50%,#33402c)">
    <svg width="60" height="60" viewBox="0 0 60 60" style="position:absolute;left:171px;top:113px"><circle cx="30" cy="30" r="27" fill="none" stroke="#fff" stroke-width="4"/><path d="M24 18l16 12-16 12z" fill="#fff"/></svg>
  </div>
</section>

<section class="feature" style="top:1670px;height:420px">
  <div class="photo" role="img" aria-label="Photo of a festive office party with dancing colleagues" style="left:99px;top:59px;width:415px;height:298px;background:linear-gradient(135deg,#d8d6d2,#6b6e72 50%,#2c2f3a)"></div>
  <div class="feature-copy" style="left:547px;top:56px">
    <h2>Corporate Events</h2><span class="rule"></span>
    <div class="meta">&#9719; 2 months ago &nbsp;&#9679; 4 min read</div>
    <p>Sed ut perspiciatis unde omnis iste natus error sit voluptatem accusantium doloremque lau dantium, totam rem aperiam.</p>
    <p>Nemo enim ipsam voluptatem quia voluptas sit aspernatur aut odit aut fugit, sed quia conse quuntur magni dolores eos qui ratione voluptatem sequi nesciunt. Neque porro quisquam est, qui dolorem ipsum quia dolor sit amet.</p>
    <span class="btn">Read More</span>
  </div>
</section>

<section class="feature tint" style="top:2092px;height:442px">
  <div class="feature-copy" style="left:99px;top:80px">
    <h2>Birthday, Reunion Parties</h2><span class="rule"></span>
    <p>Sed ut perspiciatis unde omnis iste natus error sit voluptatem accusantium doloremque lau dantium, totam rem aperiam, eaque ipsa quae ab illo inventore veritatis et quasi archi tecto beatae vitae dicta sunt explicabo.</p>
    <p>Nemo enim ipsam voluptatem quia voluptas sit aspernatur aut odit aut fugit, sed quia conse quuntur magni dolores eos qui ratione voluptatem sequi nesciunt. Neque porro quisquam est, qui dolorem ipsum quia dolor sit amet.</p>
    <span class="btn">Read More</span>
  </div>
  <div class="photo" role="img" aria-label="Photo of a birthday party with balloons and sparklers on a cake" style="left:683px;top:69px;width:415px;height:293px;background:linear-gradient(135deg,#b07b6a,#5a2f5e 50%,#241430)"></div>
</section>

<h2 class="section-title gallery-title" style="font-size:24px">Our Gallery<span class="rule" style="margin:14px auto 0"></span></h2>
<div class="gallery">
  <div class="tile" role="img" aria-label="Photo of party guests in hats dancing" style="left:0;top:0;width:334px;height:521px;background:linear-gradient(160deg,#8a7a5e,#c2a24a 55%,#3b3022)"></div>
  <div class="tile tile-brand" style="left:334px;top:0;width:333px;height:260px">Maple Lantern<br>Productions</div>
  <div class="tile" role="img" aria-label="Photo of friends raising glasses at a party" style="left:667px;top:0;width:333px;height:260px;background:linear-gradient(135deg,#d9cdb8,#8b6e56 60%,#3e2f28)"></div>
  <div class="tile" role="img" aria-label="Photo of people dancing at an office event" style="left:334px;top:260px;width:333px;height:261px;background:linear-gradient(135deg,#dad8d0,#7b7f86 55%,#2d3340)"></div>
  <div class="tile" role="img" aria-label="Photo of a night party with sparklers and lights" style="left:667px;top:260px;width:333px;height:261px;background:linear-gradient(135deg,#6a4a3a,#3a2530 55%,#140f14)"></div>
</div>

<footer class="site-footer">
  <div class="foot-brand"><div class="dot"></div><div class="name">Maple Lantern Productions</div></div>
  <div class="foot-col" style="left:375px">
    <h4>Usefull Links</h4><span class="rule"></span>
    <ul class="links"><li>Home</li><li>About Us</li><li>Services</li><li>Events</li><li>Gallery</li><li>Contact Us</li></ul>
  </div>
  <div class="foot-col" style="left:554px;width:240px">
    <h4>Contact Us</h4><span class="rule"></span>
    <div class="info"><span class="ic"><svg width="14" height="18" viewBox="0 0 14 18"><path d="M7 0a7 7 0 017 7c0 5-7 11-7 11S0 12 0 7a7 7 0 017-7z" fill="#262626"/><circle cx="7" cy="7" r="2.5" fill="#fff"/></svg></span><div><b>Address,</b><span>19 Harrow Field Road, CT<br>HUB 4, England 5678</span></div></div>
    <div class="info"><span class="ic"><svg width="12" height="18" viewBox="0 0 12 18"><rect x="1" y="1" width="10" height="16" rx="2" fill="none" stroke="#262626" stroke-width="2"/></svg></span><div><b>Phone Number:</b><span>180 555 0142</span></div></div>
    <div class="info"><span class="ic"><svg width="16" height="12" viewBox="0 0 16 12"><rect width="16" height="12" fill="#262626"/><path d="M0 0l8 6 8-6" fill="none" stroke="#fff" stroke-width="1.5"/></svg></span><div><b>Email:</b><span>info@maplelantern.example</span></div></div>
  </div>
  <div class="foot-col" style="left:815px">
    <h4>Contact Form</h4><span class="rule"></span>
    <div class="form">
      <div class="field">Name</div><div class="field">Phone</div>
      <div class="field wide">Message</div>
      <div class="send">Send Message</div>
    </div>
  </div>
  <div class="foot-rule"></div>
  <p class="copyright">Copyrights @ 2017 Maple Lantern. All Rights Reserved.</p>
</footer>

</body>
</html>
```